Veluxa Bone & Motion Business Card

Need a business card using the logo provided. I want brand side of the card to be grey with the logo in the center of the card in white.

On the other side I leave to the designers

Target Market(s)

Personal Injury Attorneys

Industry/Entity Type

Medical

Contact Information for Business Card

Name, CEO. Cell Phone, (Hialeah, Address, Phone) (Homestead, Address, Phone) (Tallahassee, Address, Phone)

Colors

Designer to choose only greyscale colors for use in the design.

Requirements
Must have
• Logo by itself on one side

```html
<!DOCTYPE html>
<html lang="en">
<head>
<meta charset="utf-8">
<title>Veluxa Bone &amp; Motion – Business Card</title>
<link rel="stylesheet" href="https://fonts.googleapis.com/css2?family=Lato:wght@400;700&family=Source+Sans+3:wght@400;600;700&display=swap">
<style>
  :root {
    --backdrop: #1f1f21;
    --card-grey: #55585b;
    --card-white: #f1f2f2;
    --accent: #8da8b0;
    --logo-tint: #7f9ca5;
    --ink: #2b2b2d;
    --light-text: #e4e6e7;
  }
  * { margin: 0; padding: 0; box-sizing: border-box; }
  html, body { width: 1200px; height: 800px; overflow: hidden; }
  body {
    background: var(--backdrop);
    font-family: "Source Sans 3", sans-serif;
    position: relative;
  }
  .card {
    position: absolute;
    top: 246px;
    width: 540px;
    height: 309px;
    overflow: hidden;
    box-shadow: 0 10px 30px rgba(0,0,0,.45);
  }
  .card-front { left: 40px; background: var(--card-grey); }
  .card-back { left: 620px; background: var(--card-white); }

  .wordmark {
    font-family: "Lato", sans-serif;
    font-weight: 400;
    text-transform: uppercase;
    white-space: nowrap;
  }
  .card-front .wordmark {
    position: absolute;
    left: 0; right: 0; top: 50%;
    transform: translateY(-50%);
    text-align: center;
    color: #ffffff;
    font-size: 34px;
    letter-spacing: 4px;
  }
  .card-back .wordmark {
    position: absolute;
    right: 30px; top: 34px;
    color: var(--logo-tint);
    font-size: 19px;
    letter-spacing: 2px;
  }

  .wave { position: absolute; inset: 0; }

  .person {
    position: absolute;
    left: 30px; top: 86px;
    line-height: 1.25;
  }
  .person-name { color: var(--logo-tint); font-weight: 700; font-size: 15px; }
  .person-title { color: var(--ink); font-size: 13px; }
  .person-phone {
    color: var(--ink); font-weight: 700; font-size: 13px;
    display: flex; align-items: center; gap: 6px;
  }

  .office {
    position: absolute;
    color: var(--light-text);
    font-size: 12px;
    line-height: 1.3;
  }
  .office-phone { display: flex; align-items: center; gap: 5px; }
  .office-1 { left: 140px; top: 180px; }
  .office-2 { left: 140px; top: 240px; }
  .office-3 { left: 340px; top: 166px; }
  .icon { width: 10px; height: 10px; flex: none; }
</style>
</head>
<body>

<section class="card card-front" aria-label="Brand side">
  <p class="wordmark">Veluxa Bone &amp; Motion</p>
</section>

<section class="card card-back" aria-label="Contact side">
  <svg class="wave" viewBox="0 0 540 309" preserveAspectRatio="none">
    <path d="M0,256 C60,176 150,146 260,141 C360,136 420,156 470,116 C510,86 522,64 540,44"
          fill="none" stroke="var(--accent)" stroke-width="5"/>
    <path d="M0,264 C60,184 150,154 260,149 C360,144 420,164 470,124 C510,94 522,72 540,52 L540,309 L0,309 Z"
          fill="var(--card-grey)"/>
  </svg>

  <p class="wordmark">Veluxa Bone &amp; Motion</p>

  <div class="person">
    <p class="person-name">Clara Whitfield</p>
    <p class="person-title">Chief Executive Officer</p>
    <p class="person-phone">
      <svg class="icon" viewBox="0 0 10 14" style="height:13px"><rect x="1" y="0.5" width="8" height="13" rx="1.5" fill="none" stroke="#9aa0a3" stroke-width="1"/></svg>
      +1 555-014-2290
    </p>
  </div>

  <div class="office office-1">
    <p class="office-phone"><svg class="icon" viewBox="0 0 10 10"><path d="M2 1 L4 3 L3 4 Q4 6 6 7 L7 6 L9 8 L8 9 Q3 9 1 2 Z" fill="var(--accent)"/></svg>555-014-2201</p>
    <p>214 Birch Lane</p>
    <p>Tallahassee, FL 9101</p>
  </div>
  <div class="office office-2">
    <p class="office-phone"><svg class="icon" viewBox="0 0 10 10"><path d="M2 1 L4 3 L3 4 Q4 6 6 7 L7 6 L9 8 L8 9 Q3 9 1 2 Z" fill="var(--accent)"/></svg>555-014-2202</p>
    <p>78 Orchard Way</p>
    <p>Homestead, FL 9102</p>
  </div>
  <div class="office office-3">
    <p class="office-phone"><svg class="icon" viewBox="0 0 10 10"><path d="M2 1 L4 3 L3 4 Q4 6 6 7 L7 6 L9 8 L8 9 Q3 9 1 2 Z" fill="var(--accent)"/></svg>555-014-2203</p>
    <p>36 Harbor Road</p>
    <p>Hialeah, Florida 9103</p>
  </div>
</section>

</body>
</html>
```